Brookvale Estates LLC stationary for a real estate property management company.

Create stationary (letterhead, envelopes, business cards) using Brookvale Estates LLC logo as primary creative element. Stationary design needs to be horizontal, leaving as much space as possible for correspondence copy. See attached Creative Brief and past stationary files for details.

Target Market(s)

Prospective apartment residents and current residents, vendors, and government agencies.

Industry/Entity Type

Property Management

Contact Information for Business Card

Business card employee title: Property Manager. Should include address, phone, fax, email, website, slogan, and Brookvale Estates logo.

Font styles to use
Sans Serif

Colors
0592cd
000000

Requirements
Must have
• Tone should be conservative, institutional, business (i.e. banking, finance, real estate). Must include: address, phone, fax, website, and slogan (see attached Creative Brief). Should be a horizontal design, leaving as much room as possible for letter correspondence copy.
Nice to have
• Please use an Arial or Helvetica style font.
Should not have
• Letterhead layout should leave as much room as possible for copy.

```html
<!DOCTYPE html>
<html lang="en">
<head>
<meta charset="utf-8">
<title>Brookvale Estates LLC – Business Card</title>
<link rel="stylesheet" href="https://fonts.googleapis.com/css2?family=Arimo:wght@400;700&display=swap">
<style>
  :root {
    --backdrop: #2b2b2b;
    --blue-light: #14c0ec;
    --blue-mid: #0b7fc0;
    --blue-deep: #0a64a4;
    --brand-blue: #0d6fae;
    --ink-grey: #555555;
    --paper: #f4f4f4;
    --white: #ffffff;
  }
  * { box-sizing: border-box; margin: 0; padding: 0; }
  html, body {
    width: 1200px; height: 960px; overflow: hidden;
    background: var(--backdrop);
    font-family: "Arimo", Arial, Helvetica, sans-serif;
  }
  .canvas { position: relative; width: 1200px; height: 960px; }
  .card {
    position: absolute; width: 600px; height: 342px;
    box-shadow: 0 3px 8px rgba(0,0,0,.5);
  }
  .card-front {
    left: 302px; top: 129px;
    background: linear-gradient(135deg, var(--blue-light) 0%, var(--blue-mid) 30%, var(--blue-deep) 60%, var(--blue-deep) 100%);
    color: var(--white);
  }
  .front-brand {
    position: absolute; left: 60px; top: 120px; width: 180px;
    font-size: 22px; font-weight: 700; line-height: 1.25; color: var(--white);
  }
  .divider {
    position: absolute; left: 261px; top: 86px; width: 1px; height: 170px;
    background: linear-gradient(to bottom, rgba(255,255,255,0), rgba(255,255,255,.9) 20%, rgba(255,255,255,.9) 80%, rgba(255,255,255,0));
  }
  .details { position: absolute; left: 290px; top: 86px; }
  .person-name { font-size: 22px; font-weight: 700; letter-spacing: .2px; line-height: 26px; }
  .person-title { font-size: 15px; line-height: 20px; margin-bottom: 6px; }
  .address { font-size: 14px; line-height: 19px; margin-bottom: 6px; }
  .contact-list { list-style: none; font-size: 14px; line-height: 19px; }
  .contact-list li { display: flex; align-items: center; gap: 8px; }
  .contact-list svg { width: 14px; height: 14px; fill: var(--white); flex: none; }
  .card-back {
    left: 299px; top: 488px;
    background: var(--paper);
    display: flex; align-items: center; justify-content: center; gap: 16px;
  }
  .brand-dot { width: 54px; height: 54px; border-radius: 50%; background: var(--ink-grey); }
  .brand-name {
    font-size: 34px; font-weight: 700; color: var(--brand-blue);
    line-height: 1.05; letter-spacing: 1px;
  }
</style>
</head>
<body>
<main class="canvas">
  <section class="card card-front">
    <div class="front-brand">Brookvale Estates</div>
    <div class="divider"></div>
    <div class="details">
      <h1 class="person-name">DANIEL WHITFORD</h1>
      <p class="person-title">Property Manager</p>
      <p class="address">2750 Harbor Ridge Drive #B210<br>Lakewood, CO 80226</p>
      <ul class="contact-list">
        <li><svg viewBox="0 0 16 16" aria-hidden="true"><path d="M3.6 1.2l2.2 2.4-1.3 1.7c.9 2 2.3 3.4 4.2 4.3l1.7-1.3 2.4 2.2-1.2 2.3C6.8 12.4 3.4 9 1.9 3.7z"/></svg>555-204-7731</li>
        <li><svg viewBox="0 0 16 16" aria-hidden="true"><rect x="4" y="1" width="8" height="4"/><rect x="1" y="6" width="14" height="6" rx="1"/><rect x="4" y="10" width="8" height="5" fill="#0a64a4" stroke="#fff" stroke-width="1.5"/></svg>555-204-7732</li>
        <li><svg viewBox="0 0 16 16" aria-hidden="true"><path d="M1 3h14v1.2L8 9 1 4.2z"/><path d="M1 5.8L8 10.6l7-4.8V13H1z"/></svg>daniel@brookvaleestates.us</li>
        <li><svg viewBox="0 0 16 16" aria-hidden="true"><circle cx="8" cy="8" r="7"/><path d="M5 4c1 1 2 1 2 2.5S5 8 5 10M10 3c0 2 2 2 3 3M9 13c0-2 2-2 2-4" stroke="#0a64a4" stroke-width="1.4" fill="none"/></svg>www.brookvaleestates.us</li>
      </ul>
    </div>
  </section>

  <section class="card card-back">
    <div class="brand-dot" aria-hidden="true"></div>
    <div class="brand-name">BROOKVALE<br>ESTATES LLC</div>
  </section>
</main>
</body>
</html>
```